TALVORE GROUP OF CLINICS

We need a medical & lab report file. The design should be healthcare related. Our current file design has been used for almost 10 years. We need something more fresh & up-to-date. We have attached the current file design.

Need extra days to review

```html
<!DOCTYPE html>
<html lang="en">
<head>
<meta charset="utf-8">
<title>Talvore Group of Clinics – Medical Report Folder</title>
<link rel="stylesheet" href="https://fonts.googleapis.com/css2?family=Poppins:wght@300;400;500;600;700&display=swap">
<style>
  :root {
    --navy: #0c0e6e;
    --sky: #4fb0de;
    --sky-deep: #3ea7dc;
    --white: #ffffff;
    --page-bg: #eef1f4;
    --photo-dark: #0a1f7a;
    --photo-light: #3d8fe0;
  }
  * { margin: 0; padding: 0; box-sizing: border-box; }
  html, body { width: 890px; height: 1200px; overflow: hidden; }
  body {
    background: var(--page-bg);
    font-family: "Poppins", sans-serif;
    position: relative;
  }
  .folder-spread {
    position: absolute;
    left: 20px; top: 299px;
    width: 850px; height: 600px;
    background: var(--white);
    overflow: hidden;
    box-shadow: 0 4px 14px rgba(0,0,0,0.18);
  }
  .cover-art { position: absolute; inset: 0; }

  .group-title {
    position: absolute; left: 33px; top: 24px;
    font-weight: 600; font-size: 24px; line-height: 23px;
    letter-spacing: -0.2px;
  }
  .group-title .line-brand { color: var(--sky-deep); display: block; }
  .group-title .line-sub { color: var(--navy); display: block; }

  .clinic-card {
    position: absolute;
    width: 138px; height: 106px;
    background: var(--navy);
    border-radius: 7px;
    padding: 12px 10px 0 15px;
    color: var(--white);
  }
  .clinic-card .clinic-name {
    color: var(--sky);
    font-weight: 700; font-size: 9.3px; line-height: 10px;
  }
  .clinic-card .divider {
    width: 26px; height: 1.5px; background: var(--white);
    margin: 6px 0 8px;
  }
  .clinic-card .details {
    font-size: 5.6px; line-height: 7.3px; font-weight: 400;
  }
  .clinic-card .details b { font-weight: 600; }
  .clinic-card .number-badge {
    position: absolute; right: -7px; top: -5px;
    width: 30px; height: 30px; border-radius: 50%;
    background: var(--sky); border: 2px solid var(--white);
    color: var(--white); font-size: 15px; font-weight: 500;
    display: flex; align-items: center; justify-content: center;
  }

  .brand-mark {
    position: absolute; left: 220px; top: 478px;
    width: 120px; text-align: center;
  }
  .brand-mark .dot {
    width: 44px; height: 44px; border-radius: 50%;
    background: var(--sky); margin: 0 auto 8px;
  }
  .brand-mark .name {
    color: var(--sky-deep); font-weight: 600; font-size: 9px;
  }

  .badge-mark {
    position: absolute; left: 542px; top: 193px;
    width: 184px; height: 184px;
    display: flex; flex-direction: column; align-items: center; justify-content: center;
  }
  .badge-mark .dot {
    width: 46px; height: 46px; border-radius: 50%;
    background: var(--sky); margin-bottom: 12px;
  }
  .badge-mark .name {
    color: var(--sky-deep); font-weight: 600; font-size: 7px;
  }

  .report-heading {
    position: absolute; left: 440px; top: 400px;
    width: 402px; text-align: center;
  }
  .report-heading .tagline {
    color: var(--white); font-size: 8px; letter-spacing: 2.4px; font-weight: 400;
  }
  .report-heading .title {
    font-size: 41px; line-height: 44px; margin-top: 2px; letter-spacing: -0.5px;
  }
  .report-heading .title .strong { color: var(--white); font-weight: 700; }
  .report-heading .title .light { color: var(--navy); font-weight: 400; }
  .report-heading .subtitle {
    color: var(--white); font-size: 16px; font-weight: 500; margin-top: 0;
  }
  .report-heading .web-pill {
    display: inline-block; margin-top: 6px;
    background: var(--white); color: var(--navy);
    font-size: 10px; font-weight: 500; letter-spacing: 0.6px;
    padding: 1px 12px; border-radius: 6px;
  }
</style>
</head>
<body>
  <main class="folder-spread">
    <svg class="cover-art" width="850" height="600" viewBox="0 0 850 600">
      <defs>
        <radialGradient id="photoTone" cx="0.5" cy="0.35" r="0.7">
          <stop offset="0" stop-color="var(--photo-light)"/>
          <stop offset="1" stop-color="var(--photo-dark)"/>
        </radialGradient>
      </defs>
      <ellipse class="cover-sweep" cx="645" cy="250" rx="385" ry="305" fill="var(--sky)"/>
      <circle class="photo-ring" cx="634" cy="105" r="233" fill="var(--white)"/>
      <circle class="photo-window" cx="634" cy="105" r="205" fill="url(#photoTone)"
              role="img" aria-label="Photo of a medical professional with glowing digital health icons and a large medical cross"/>
      <circle class="badge-disc" cx="634" cy="285" r="92" fill="var(--white)"/>
    </svg>

    <h1 class="group-title">
      <span class="line-brand">TALVORE GROUP</span>
      <span class="line-sub">OF CLINICS</span>
    </h1>

    <article class="clinic-card" style="left:35px; top:88px;">
      <h2 class="clinic-name">PUSAT PERUBATAN<br>TALVORE</h2>
      <div class="divider"></div>
      <p class="details">Level 12, Wisma Orkid 3, No.8, Jalan<br>Seri Damai, Off Jalan Bukit<br>Lintang, 50480 Kuala Lumpur,<br>Tel No: <b>+603-5550 1201</b><br>Fax No: <b>+603-5550 1202</b><br>Email: &nbsp;<b>kliniktalvore@example.com</b></p>
      <span class="number-badge">1</span>
    </article>
    <article class="clinic-card" style="left:35px; top:209px;">
      <h2 class="clinic-name">PUSAT PERUBATAN<br>TALVORE</h2>
      <div class="divider"></div>
      <p class="details">Level 12, Wisma Orkid 3, No.8, Jalan<br>Seri Damai, Off Jalan Bukit<br>Lintang, 50480 Kuala Lumpur,<br>Tel No: <b>+603-5550 1201</b><br>Fax No: <b>+603-5550 1202</b><br>Email: &nbsp;<b>kliniktalvore@example.com</b></p>
      <span class="number-badge">2</span>
    </article>
    <article class="clinic-card" style="left:35px; top:331px;">
      <h2 class="clinic-name">PUSAT PERUBATAN<br>TALVORE</h2>
      <div class="divider"></div>
      <p class="details">Level 12, Wisma Orkid 3, No.8, Jalan<br>Seri Damai, Off Jalan Bukit<br>Lintang, 50480 Kuala Lumpur,<br>Tel No: <b>+603-5550 1201</b><br>Fax No: <b>+603-5550 1202</b><br>Email: &nbsp;<b>kliniktalvore@example.com</b></p>
      <span class="number-badge">3</span>
    </article>
    <article class="clinic-card" style="left:35px; top:452px;">
      <h2 class="clinic-name">PUSAT PERUBATAN<br>TALVORE</h2>
      <div class="divider"></div>
      <p class="details">Level 12, Wisma Orkid 3, No.8, Jalan<br>Seri Damai, Off Jalan Bukit<br>Lintang, 50480 Kuala Lumpur,<br>Tel No: <b>+603-5550 1201</b><br>Fax No: <b>+603-5550 1202</b><br>Email: &nbsp;<b>kliniktalvore@example.com</b></p>
      <span class="number-badge">4</span>
    </article>
    <article class="clinic-card" style="left:218px; top:88px;">
      <h2 class="clinic-name">PUSAT PERUBATAN<br>TALVORE</h2>
      <div class="divider"></div>
      <p class="details">Level 12, Wisma Orkid 3, No.8, Jalan<br>Seri Damai, Off Jalan Bukit<br>Lintang, 50480 Kuala Lumpur,<br>Tel No: <b>+603-5550 1201</b><br>Fax No: <b>+603-5550 1202</b><br>Email: &nbsp;<b>kliniktalvore@example.com</b></p>
      <span class="number-badge">5</span>
    </article>
    <article class="clinic-card" style="left:218px; top:209px;">
      <h2 class="clinic-name">PUSAT PERUBATAN<br>TALVORE</h2>
      <div class="divider"></div>
      <p class="details">Level 12, Wisma Orkid 3, No.8, Jalan<br>Seri Damai, Off Jalan Bukit<br>Lintang, 50480 Kuala Lumpur,<br>Tel No: <b>+603-5550 1201</b><br>Fax No: <b>+603-5550 1202</b><br>Email: &nbsp;<b>kliniktalvore@example.com</b></p>
      <span class="number-badge">6</span>
    </article>
    <article class="clinic-card" style="left:218px; top:331px;">
      <h2 class="clinic-name">PUSAT PERUBATAN<br>TALVORE</h2>
      <div class="divider"></div>
      <p class="details">Level 12, Wisma Orkid 3, No.8, Jalan<br>Seri Damai, Off Jalan Bukit<br>Lintang, 50480 Kuala Lumpur,<br>Tel No: <b>+603-5550 1201</b><br>Fax No: <b>+603-5550 1202</b><br>Email: &nbsp;<b>kliniktalvore@example.com</b></p>
      <span class="number-badge">7</span>
    </article>

    <div class="brand-mark">
      <div class="dot"></div>
      <p class="name">TALVORE GROUP</p>
    </div>

    <div class="badge-mark">
      <div class="dot"></div>
      <p class="name">TALVORE GROUP</p>
    </div>

    <section class="report-heading">
      <p class="tagline">YOUR HEALTHCARE PARTNER</p>
      <h2 class="title"><span class="strong">MEDICAL</span> <span class="light">REPORT</span></h2>
      <p class="subtitle">PRIVATE &amp; CONFIDENTIAL</p>
      <span class="web-pill">www.talvoregrp.com</span>
    </section>
  </main>
</body>
</html>
```